Corvana - Waste to Fuel Power Needs A Website

Make website explaining the concept and the team behind the company
Updates

I will be providing A logo and Information about the company upon signed NDA.

Coding

Coded - Design and coding required

Number of Pages Required

5+ page

```html
<!DOCTYPE html>
<html lang="en">
<head>
<meta charset="utf-8">
<title>Corvana - Waste to Fuel Power</title>
<link href="https://fonts.googleapis.com/css2?family=Krona+One&family=Roboto:wght@400;500;700&display=swap" rel="stylesheet">
<style>
:root{
  --blue:#1e5fae;
  --blue-dark:#123f82;
  --blue-light:#3f8ae0;
  --green:#7dc241;
  --green-light:#a6dc5c;
  --ink:#1d1d1d;
  --muted:#5c5c5c;
  --pale:#e9f1fc;
  --white:#ffffff;
}
*{box-sizing:border-box;margin:0;padding:0}
html,body{width:1200px;height:5046px;overflow:hidden}
body{position:relative;font-family:'Roboto',Arial,sans-serif;color:var(--ink);background:var(--white)}
.abs{position:absolute}
.display{font-family:'Krona One','Arial Black',sans-serif;letter-spacing:1px}
.title{position:absolute;left:0;width:1200px;text-align:center;font-size:38px}
.title .b{color:var(--blue)} .title .g{color:var(--green)}
.title-dot{position:absolute;left:589px;width:22px;height:22px;border-radius:50%;background:var(--green)}
.pill-btn{position:absolute;height:52px;border-radius:26px;color:#fff;font-size:14px;font-weight:700;display:flex;align-items:center;padding-left:32px;box-shadow:0 4px 10px rgba(0,0,0,.2)}
.pill-btn::after{content:"";position:absolute;right:6px;top:6px;width:40px;height:40px;border-radius:50%;background:#fff}
.btn-green{background:linear-gradient(180deg,var(--green-light),#5aa52a)}
.btn-blue{background:linear-gradient(180deg,var(--blue-light),var(--blue))}

/* header */
.header{position:absolute;left:0;top:0;width:1200px;height:128px;background:#fff;z-index:3}
.brand{position:absolute;left:145px;top:38px}
.brand-name{font-family:'Krona One',sans-serif;font-size:42px;color:var(--blue);line-height:1}
.brand-tag{font-size:18px;color:var(--green);font-weight:500;margin-top:8px;letter-spacing:.5px}
.contact-chip{position:absolute;top:20px;display:flex;align-items:center;gap:14px}
.chip-icon{width:34px;height:34px;border-radius:50%;display:flex;align-items:center;justify-content:center}
.chip-label{font-size:12px;font-weight:700}
.chip-value{font-size:16px}
.nav{position:absolute;left:515px;top:80px;width:685px;height:48px;background:linear-gradient(90deg,var(--blue),var(--blue-dark));display:flex;align-items:center}
.nav a{color:#fff;text-decoration:none;font-size:13px;font-weight:500;padding:0 15px;height:48px;line-height:48px}
.nav a.active{background:var(--green);padding:0 24px}

/* hero */
.hero{position:absolute;left:0;top:128px;width:1200px;height:800px;background:linear-gradient(120deg,#0b1f4d 0%,#1a3f8a 45%,#4a79c9 62%,#1d2f63 80%,#0a1636 100%)}
.hero h1{position:absolute;left:145px;top:150px;font-size:40px;line-height:52px;color:#fff;text-shadow:0 3px 6px rgba(0,0,0,.5)}
.hero h1 span{color:var(--green-light)}
.hero p{position:absolute;left:145px;top:265px;font-size:18px;line-height:32px;color:#fff}

/* about */
.about-art{position:absolute;left:140px;top:900px;width:380px;height:495px;background:linear-gradient(160deg,#2d5fa8 0%,#5a9a3a 55%,#1e4a8e 100%);clip-path:polygon(50% 0,100% 55%,80% 100%,20% 100%,0 55%);opacity:.9}
.about-title{position:absolute;left:565px;top:920px;font-size:38px}
.about-text{position:absolute;left:565px;top:995px;width:490px;font-size:17px;line-height:32px;color:var(--muted);text-align:justify}

/* services */
.services-band{position:absolute;left:0;top:1500px;width:1200px;height:755px;background:var(--pale)}
.svc-card{position:absolute;width:450px;height:180px;background:#fff;border-radius:90px;border:2px solid #dde6f3;box-shadow:0 6px 18px rgba(30,95,174,.08)}
.svc-card.featured{border-color:var(--green-light);box-shadow:0 0 28px rgba(125,194,65,.35)}
.svc-photo{position:absolute;top:15px;width:150px;height:150px;border-radius:50%}
.svc-body{position:absolute;top:28px;width:210px}
.svc-body h3{font-size:19px;font-weight:700;line-height:25px;margin-bottom:10px}
.svc-body p{font-size:15px;line-height:25px;color:var(--muted)}
.more{display:inline-block;margin-top:6px;font-size:14px;font-weight:700;color:var(--blue);text-decoration:underline}

/* why */
.why-item{position:absolute;width:330px}
.why-item h3{font-size:18px;font-weight:700;line-height:26px}
.why-item p{font-size:13px;line-height:22px;color:var(--muted);margin-top:6px}
.why-left{text-align:right}
.why-icon{position:absolute;width:66px;height:66px;border-radius:50%;display:flex;align-items:center;justify-content:center}
.why-icon.g{background:var(--green)} .why-icon.b{background:var(--blue)}

/* team */
.team-band{position:absolute;left:0;top:2900px;width:1200px;height:880px}
.member{position:absolute;top:3355px;width:230px;text-align:center;color:#fff}
.member-ring{width:190px;height:190px;margin:0 auto;border-radius:50%;border:2px solid rgba(255,255,255,.7);padding:10px}
.member-photo{width:100%;height:100%;border-radius:50%}
.member h3{font-size:21px;font-weight:700;margin-top:28px}
.member p{font-size:15px;line-height:22px;margin-top:6px;opacity:.9}
.member-badge{position:absolute;left:103px;top:168px;width:26px;height:26px;border-radius:50%;background:var(--green);border:2px solid #fff}

/* contact */
.field{position:absolute;height:52px;border:2px solid #d6d6d6;background:#fff;font-size:15px;color:#444;padding:14px 20px}

/* footer */
.footer{position:absolute;left:0;top:4440px;width:1200px;height:606px}
.foot-nav{position:absolute;left:0;top:4705px;width:1200px;height:66px;border-top:1px solid rgba(255,255,255,.25);border-bottom:1px solid rgba(255,255,255,.25);display:flex;justify-content:center;align-items:center;gap:36px}
.foot-nav a{color:#fff;text-decoration:none;font-size:21px;font-weight:500}
.foot-contacts{position:absolute;left:0;top:4805px;width:1200px;display:flex;justify-content:center;gap:50px;color:#fff;font-size:20px}
.foot-contacts span{display:flex;align-items:center;gap:14px}
.ring-ico{width:42px;height:42px;border-radius:50%;border:2px solid #fff;display:flex;align-items:center;justify-content:center}
.copy{position:absolute;left:0;top:4893px;width:1200px;text-align:center;color:#fff;font-size:17px}
.socials{position:absolute;left:0;top:4950px;width:1200px;display:flex;justify-content:center;gap:10px}
.socials span{width:38px;height:38px;border-radius:50%;background:#fff}
</style>
</head>
<body>

<header class="header">
  <div class="brand">
    <div class="brand-name">CORVANA</div>
    <div class="brand-tag">WASTE TO FUEL POWER</div>
  </div>
  <div class="contact-chip" style="left:665px">
    <div class="chip-icon" style="background:var(--blue)">
      <svg width="16" height="16" viewBox="0 0 24 24"><path fill="#fff" d="M6.6 10.8a15 15 0 006.6 6.6l2.2-2.2a1 1 0 011-.25 11.4 11.4 0 003.6.6 1 1 0 011 1V20a1 1 0 01-1 1A17 17 0 013 4a1 1 0 011-1h3.5a1 1 0 011 1 11.4 11.4 0 00.6 3.6 1 1 0 01-.25 1z"/></svg>
    </div>
    <div><div class="chip-label" style="color:var(--blue)">CALL US</div><div class="chip-value">+1 555 010 0199</div></div>
  </div>
  <div class="contact-chip" style="left:862px">
    <div class="chip-icon" style="background:var(--green)">
      <svg width="16" height="16" viewBox="0 0 24 24"><path fill="#fff" d="M3 5h18v14H3z"/><path fill="none" stroke="var(--green)" stroke-width="2" d="M3 6l9 7 9-7"/></svg>
    </div>
    <div><div class="chip-label" style="color:var(--green)">EMAIL US</div><div class="chip-value">office@corvana.com</div></div>
  </div>
  <nav class="nav">
    <a class="active">HOME</a><a>ABOUT US</a><a>SERVICES</a><a>WHY US</a><a>REVIEWS</a><a>CONTACT US</a>
  </nav>
</header>

<section class="hero" role="img" aria-label="Night view of an illuminated refinery with cooling towers">
  <h1 class="display">TURNING PLASTIC WASTE<br><span>INTO FUEL ENERGY</span></h1>
  <p>Corvana converts plastic waste into high-quality diesel fuel,<br>creating sustainable energy while reducing environmental pollution.</p>
  <div class="pill-btn btn-green" style="left:145px;top:368px;width:265px">LEARN HOW IT WORKS</div>
  <div class="pill-btn btn-blue" style="left:425px;top:368px;width:265px">PARTNER WITH US</div>
  <svg class="abs" style="left:588px;top:592px" width="24" height="50" viewBox="0 0 24 50"><rect x="3" y="1" width="18" height="30" rx="9" fill="none" stroke="#fff" stroke-width="2"/><line x1="12" y1="8" x2="12" y2="14" stroke="#fff" stroke-width="2"/><path d="M6 40l6 6 6-6" fill="none" stroke="#fff" stroke-width="2"/></svg>
</section>
<svg class="abs" style="left:0;top:640px" width="1200" height="300" viewBox="0 0 1200 300">
  <path d="M0 210 C250 80 500 60 760 110 C950 150 1100 110 1200 60 L1200 300 L0 300Z" fill="var(--blue-light)" opacity=".8"/>
  <path d="M0 240 C250 100 520 90 760 130 C950 165 1100 130 1200 90 L1200 300 L0 300Z" fill="var(--green-light)"/>
  <path d="M0 270 C260 130 520 110 760 150 C960 185 1110 155 1200 120 L1200 300 L0 300Z" fill="#fff"/>
</svg>

<section>
  <div class="about-art" role="img" aria-label="Recycling-flame emblem filled with a landscape photo"></div>
  <div class="title-dot" style="left:845px;top:890px"></div>
  <h2 class="about-title display"><span style="color:var(--blue)">ABOUT</span> <span style="color:var(--green)">US</span></h2>
  <p class="about-text">Dana Whitlock is a proven entrepreneur who has founded and scaled consumer brands, including marigoldhome.com and tidewell.com, from concept to commercialization, bringing a strong execution focus and hands-on experience across early-stage growth and scale-up. An integrated plastic waste conversion entity in the US. Secured feedstock supply chains and confirmed offtake partners, ensuring consistent operation and reliable revenue. Dual benefit opportunity - powerful environmental impact combined with strong, repeatable profitability.</p>
  <div class="pill-btn btn-green" style="left:565px;top:1340px;width:165px">READ MORE</div>
</section>

<div class="services-band"></div>
<svg class="abs" style="left:0;top:1370px" width="1200" height="200" viewBox="0 0 1200 200">
  <path d="M0 200 L0 130 C200 40 420 80 620 140 C820 200 1020 170 1200 60 L1200 200Z" fill="var(--pale)"/>
  <path d="M110 120 C300 40 480 70 620 120" fill="none" stroke="var(--blue)" stroke-width="6"/>
  <path d="M760 180 C950 200 1100 150 1200 80" fill="none" stroke="var(--green)" stroke-width="8"/>
</svg>
<section>
  <div class="title-dot" style="top:1650px"></div>
  <h2 class="title display" style="top:1677px"><span class="b">OUR</span> <span class="g">SERVICES</span></h2>

  <div class="svc-card" style="left:140px;top:1780px">
    <div class="svc-body" style="left:62px"><h3>Waste Management &amp; Recycling</h3><p>Diverting plastic waste from landfills.</p><span class="more">READ MORE</span></div>
    <div class="svc-photo" role="img" aria-label="Worker sorting plastic waste" style="right:12px;background:linear-gradient(135deg,#8a96a6,#d9dde3 50%,#e0702a)"></div>
  </div>
  <div class="svc-card featured" style="left:610px;top:1780px">
    <div class="svc-photo" role="img" aria-label="Refinery at dusk" style="left:12px;background:linear-gradient(160deg,#5d7ea8,#2a3b58 60%,#c58a4a)"></div>
    <div class="svc-body" style="left:182px;top:36px"><h3>Fuel Production</h3><p>Output – a commercial grade diesel fuel.</p><span class="more">READ MORE</span></div>
  </div>
  <div class="svc-card" style="left:140px;top:1980px">
    <div class="svc-body" style="left:62px;top:36px"><h3>Scalable Technology</h3><p>Modular, Independent units used in operations</p><span class="more">READ MORE</span></div>
    <div class="svc-photo" role="img" aria-label="Aerial view of a treatment plant" style="right:12px;background:linear-gradient(135deg,#5f7a3a,#8ea06a 50%,#3d5a6a)"></div>
  </div>
  <div class="svc-card" style="left:610px;top:1980px">
    <div class="svc-photo" role="img" aria-label="Team working in an office" style="left:12px;background:linear-gradient(135deg,#dfe8f2,#9fb6cf 60%,#4d6d93)"></div>
    <div class="svc-body" style="left:182px;top:36px"><h3>Sustainability Solutions</h3><p>Clean Fuel and Environmental impact</p><span class="more">READ MORE</span></div>
  </div>
  <div class="abs" style="left:570px;top:1930px;width:60px;height:60px;border-radius:50%;background:var(--green);border:4px solid var(--pale)"></div>
</section>

<section>
  <div class="title-dot" style="top:2370px"></div>
  <h2 class="title display" style="top:2397px"><span class="b">WHY</span> <span class="g">CHOOSE US</span></h2>

  <svg class="abs" style="left:470px;top:2560px" width="260" height="260" viewBox="0 0 260 260">
    <circle cx="130" cy="130" r="122" fill="none" stroke="var(--blue)" stroke-width="5"/>
    <circle cx="130" cy="130" r="104" fill="#fff" stroke="#e2e8f0" stroke-width="2"/>
    <circle cx="130" cy="130" r="60" fill="var(--blue)"/>
    <circle cx="105" cy="21" r="6" fill="#fff" stroke="var(--blue)" stroke-width="2"/>
    <circle cx="155" cy="21" r="6" fill="#fff" stroke="var(--blue)" stroke-width="2"/>
    <circle cx="8" cy="130" r="6" fill="#fff" stroke="var(--blue)" stroke-width="2"/>
    <circle cx="252" cy="130" r="6" fill="#fff" stroke="var(--blue)" stroke-width="2"/>
    <circle cx="55" cy="225" r="6" fill="#fff" stroke="var(--blue)" stroke-width="2"/>
    <circle cx="205" cy="225" r="6" fill="#fff" stroke="var(--blue)" stroke-width="2"/>
  </svg>

  <div class="why-item why-left" style="left:90px;top:2505px"><h3>24/7 High-Utilization<br>Revenue Engine</h3><p>Continuous operation (24/7)</p><span class="more">READ MORE</span></div>
  <div class="why-icon g" style="left:443px;top:2542px"><svg width="28" height="28" viewBox="0 0 24 24"><rect x="3" y="5" width="18" height="16" rx="2" fill="none" stroke="#fff" stroke-width="2"/><path d="M3 10h18M8 3v4M16 3v4" stroke="#fff" stroke-width="2"/></svg></div>

  <div class="why-item why-left" style="left:32px;top:2648px"><h3>Low CAPEX, Modular<br>Replication Model</h3><p>Each module operates independently</p><span class="more">READ MORE</span></div>
  <div class="why-icon b" style="left:385px;top:2670px"><svg width="26" height="26" viewBox="0 0 24 24"><rect x="5" y="3" width="14" height="18" fill="none" stroke="#fff" stroke-width="2"/><path d="M9 7h2M13 7h2M9 11h2M13 11h2M10 21v-4h4v4" stroke="#fff" stroke-width="2"/></svg></div>

  <div class="why-item why-left" style="left:102px;top:2790px"><h3>Industry Experience</h3><p>The platform is built and operated<br>by a team with hands-on</p><span class="more">READ MORE</span></div>
  <div class="why-icon g" style="left:447px;top:2788px"><svg width="28" height="28" viewBox="0 0 24 24"><path d="M3 21V10l5 3V10l5 3V10l5 3V4h3v17z" fill="#fff"/></svg></div>

  <div class="why-icon b" style="left:745px;top:2542px"><svg width="28" height="28" viewBox="0 0 24 24"><circle cx="12" cy="12" r="9" fill="none" stroke="#fff" stroke-width="2"/><circle cx="12" cy="12" r="5" fill="none" stroke="#fff" stroke-width="2"/><circle cx="12" cy="12" r="1.5" fill="#fff"/></svg></div>
  <div class="why-item" style="left:835px;top:2505px"><h3>Sustainability Focus</h3><p>A structurally sustainable model<br>delivering measurable waste</p><span class="more">READ MORE</span></div>

  <div class="why-icon g" style="left:782px;top:2670px"><svg width="28" height="28" viewBox="0 0 24 24"><circle cx="12" cy="12" r="9" fill="none" stroke="#fff" stroke-width="2"/><path d="M3 12h18M12 3c3 3 3 15 0 18M12 3c-3 3-3 15 0 18" fill="none" stroke="#fff" stroke-width="1.6"/></svg></div>
  <div class="why-item" style="left:867px;top:2650px"><h3>Global Reach with<br>Local Strength</h3><p>A globally scalable platform</p><span class="more">READ MORE</span></div>

  <div class="why-icon b" style="left:745px;top:2788px"><svg width="26" height="26" viewBox="0 0 24 24"><rect x="4" y="10" width="16" height="11" rx="2" fill="#fff"/><path d="M8 10V7a4 4 0 018 0v3" fill="none" stroke="#fff" stroke-width="2"/></svg></div>
  <div class="why-item" style="left:826px;top:2786px"><h3>Feedstock &amp; Offtake<br>De-Risked Upfront</h3><p>With plastic feedstock supply and<br>diesel buyers already secured,</p><span class="more">READ MORE</span></div>
</section>

<svg class="team-band" viewBox="0 0 1200 880" preserveAspectRatio="none">
  <defs><linearGradient id="teamGrad" x1="0" y1="0" x2="1" y2="1"><stop offset="0" stop-color="#1e5fae"/><stop offset=".5" stop-color="#3d88a8"/><stop offset="1" stop-color="#a6dc5c"/></linearGradient></defs>
  <path d="M0 0 C150 80 300 120 520 130 C800 140 1000 80 1200 100 L1200 880 L0 880Z" fill="url(#teamGrad)"/>
  <path d="M520 130 C800 140 1000 60 1200 90 L1200 100 C1000 80 800 150 520 140Z" fill="#dff2c8"/>
</svg>
<section>
  <div class="title-dot" style="top:3195px;background:#fff"></div>
  <h2 class="title display" style="top:3235px"><span style="color:#fff">MEET</span> <span style="color:var(--green-light)">OUR TEAM</span></h2>
  <div class="member" style="left:132px"><div class="member-ring"><div class="member-photo" role="img" aria-label="Portrait of Anika" style="background:linear-gradient(160deg,#e8eef6,#9fb1c8)"></div></div><div class="member-badge"></div><h3>Anika</h3><p>Sed ut perspiciatis unde omnis iste natus voluptatem</p></div>
  <div class="member" style="left:367px"><div class="member-ring"><div class="member-photo" role="img" aria-label="Portrait of Bertrand" style="background:linear-gradient(160deg,#f1f3f6,#b7c0cc)"></div></div><div class="member-badge"></div><h3>Bertrand</h3><p>Sed ut perspiciatis unde omnis iste natus voluptatem</p></div>
  <div class="member" style="left:602px"><div class="member-ring"><div class="member-photo" role="img" aria-label="Portrait of a representative of The Lumen Group" style="background:linear-gradient(160deg,#4d79b3,#1d3e6e)"></div></div><div class="member-badge"></div><h3>The Lumen Group</h3><p>Sed ut perspiciatis unde omnis iste natus voluptatem</p></div>
  <div class="member" style="left:838px"><div class="member-ring"><div class="member-photo" role="img" aria-label="Portrait of Dorin" style="background:linear-gradient(160deg,#2e4768,#101b2b)"></div></div><div class="member-badge"></div><h3>Dorin</h3><p>Sed ut perspiciatis unde omnis iste natus voluptatem</p></div>
</section>

<section>
  <div class="title-dot" style="top:3895px"></div>
  <h2 class="title display" style="top:3925px"><span class="b">CONTACT</span> <span class="g">US</span></h2>
  <div class="field" style="left:233px;top:4030px;width:360px">First Name</div>
  <div class="field" style="left:605px;top:4030px;width:360px">Last Name</div>
  <div class="field" style="left:233px;top:4095px;width:360px">Email address</div>
  <div class="field" style="left:605px;top:4095px;width:360px">Phone Number</div>
  <div class="field" style="left:233px;top:4160px;width:732px;height:112px">Message</div>
  <div class="pill-btn btn-green" style="left:517px;top:4310px;width:166px;padding-left:44px">SUBMIT</div>
</section>

<svg class="footer" viewBox="0 0 1200 606" preserveAspectRatio="none">
  <path d="M0 80 C250 -10 500 0 750 50 C950 90 1100 60 1200 10 L1200 606 L0 606Z" fill="var(--green-light)"/>
  <path d="M0 100 C250 10 500 20 750 70 C950 110 1100 80 1200 40 L1200 606 L0 606Z" fill="var(--blue)"/>
</svg>
<section>
  <div class="abs" style="left:0;top:4585px;width:1200px;text-align:center">
    <div class="brand-name" style="color:#fff">CORVANA</div>
    <div class="brand-tag">WASTE TO FUEL POWER</div>
  </div>
  <nav class="foot-nav"><a>HOME</a><a>ABOUT US</a><a>SERVICES</a><a>WHY US</a><a>REVIEWS</a><a>CONTACT US</a></nav>
  <div class="foot-contacts">
    <span><span class="ring-ico"><svg width="16" height="16" viewBox="0 0 24 24"><rect x="3" y="5" width="18" height="14" fill="#fff"/><path d="M3 6l9 7 9-7" fill="none" stroke="var(--blue)" stroke-width="2"/></svg></span>office@corvana.com</span>
    <span style="font-weight:700"><span class="ring-ico" style="background:var(--green);border-color:var(--green)"><svg width="16" height="16" viewBox="0 0 24 24"><path fill="#fff" d="M6.6 10.8a15 15 0 006.6 6.6l2.2-2.2a1 1 0 011-.25 11.4 11.4 0 003.6.6 1 1 0 011 1V20a1 1 0 01-1 1A17 17 0 013 4a1 1 0 011-1h3.5a1 1 0 011 1 11.4 11.4 0 00.6 3.6 1 1 0 01-.25 1z"/></svg></span>+1 555 010 0199</span>
    <span><span class="ring-ico"><svg width="18" height="18" viewBox="0 0 24 24"><circle cx="12" cy="12" r="9" fill="none" stroke="#fff" stroke-width="2"/><path d="M3 12h18M12 3c3 3 3 15 0 18M12 3c-3 3-3 15 0 18" fill="none" stroke="#fff" stroke-width="1.6"/></svg></span>www.corvana.com</span>
  </div>
  <p class="copy">© 2026 Companyname.All Rights Reserved &nbsp;|&nbsp; Privacy Policy &nbsp;|&nbsp; Terms of use</p>
  <div class="socials"><span aria-label="Social profile"></span><span aria-label="Video channel"></span><span aria-label="Professional network"></span></div>
</section>

</body>
</html>
```